IT consulting company looking for a modern business design for a website and a new logo

We are the IT-consulting company VelmaTrix from Germany and need a new and modern business website and a new logo. We are specialized in output management. Our services include business analysis, outsourcing, development, training and project leading. We wish for a design with nature pictures (mountains, lakes, rivers, forests, etc.) for our company with the colors green and blue. If it is possible, a slow-mo video of a nature scene. The design should be responsive and the menu should change to a hamburger menu. The following are: • Services / Solutions 1. Output Management 2. Outsourcing 3. Development 4. Business Analyst 5. Training • Partners • Careers • About Us 1. Project A 2. Project B 3. Project C • Contact Notes for the following categories: For "Services / Solutions" we want to conclude some contents from all the sub-points and sub-points below. Additionally, we would like to see some sub-point under "Services / Solutions". For Output Management: "5 Benefits of Output Management Systems (OMS) - OMS Simplifies and Accelerates External Communication - Helps Reduce Communication Mistakes - Provides Customers With Fast and Secure Responses to your questions - Employees can focus on the essential as they can access prepared templates - Companies get complete transparency about their communication "The point" partner does not have sub-points. The content here is a quote and the logo from the company Brel. For now, just placeholders on this site. The next point wants to be "career" without sub-point and wants to contain some text. Carrer options wants to be listed here. Next point wants to be "About us", where we need sub-points which we do not know exactly at this moment, but they will contain text. By clicking directly on "About us" we want to include pictures and texts about 6 employees for which we only need placeholders at the moment. The last point wants to be "contact", where customers can send us messages. The main page should include a story about our company, which can be a placeholder for now. For reference, designs have a look at: https://brelvanto.de/ https://www.tarnopix.com/ https://www.pldrive.de/ We prefer WordPress designs, created with the plugin ELEMENTOR, so that we can easily edit the content by ourselves. The final design should look professional, competent and modern.

Target Market(s)

With our website, we want to reach the following target groups. <br> <br> <br> <br> <br> <br> <br> <br> <br> <br> <br> <br> <br> <br> <br> <br> <br> <br> <br> <br> <br> <br> <br> <br> <br> <br> <br> <br> <br> <br> <br> <br> <br> <br> <br> <br> <br> <br> <br> <br> <br> <br> <br> <br> <br> <br> <br> <br> <br>

Industry/Entity Type

Consulting

Logo Text

(optionally) VelmaTrix

Font styles to use
Sans Serif

Colors

Designer to choose colors to be used in the design.

Requirements
Must have
• 1. Outsourcing 3. Development 4. Business Analyst 5. Training • Partners • Careers • About Us 1. Project A 2. Project B 3. Project C • Contact The above-mentioned background picture with nature motifs (mountains, lakes, rivers, forests, etc.). WordPress design in primary colors blue and green.
Nice to have
• ELEMENTOR template. Effects for the background pictures. Counter of all successful projects for Output Management, Business Analyst and Training

```html
<!DOCTYPE html>
<html lang="de">
<head>
<meta charset="utf-8">
<title>VelmaTrix – IT Consulting</title>
<link href="https://fonts.googleapis.com/css2?family=Barlow:wght@400;500;600;700&family=Roboto:wght@400;500&display=swap" rel="stylesheet">
<style>
:root{
  --blue:#2d8ae2;
  --blue-bright:#2f96ee;
  --blue-deep:#1e58a6;
  --ink:#1f2226;
  --text:#555b63;
  --grey-bg:#efefef;
  --white:#ffffff;
  --dark-btn:#23272b;
}
*{margin:0;padding:0;box-sizing:border-box}
html,body{width:1200px;height:4640px;overflow:hidden}
body{position:relative;background:var(--white);font-family:"Roboto",sans-serif;color:var(--text)}
.abs{position:absolute}
.heading{font-family:"Barlow",sans-serif;color:var(--ink);letter-spacing:.5px}
.heading b{font-weight:700}
.heading span{font-weight:400}
.rule{position:absolute;height:3px;background:var(--blue)}

/* header + hero */
.hero{left:0;top:0;width:1200px;height:660px;background:linear-gradient(180deg,#f4f6f8 0%,#e6ecf1 12%,#9fb5a7 25%,#4f7a45 45%,#6e9a3b 65%,#93b238 82%,#7d8f3a 100%)}
.logo{left:144px;top:38px;font-family:"Barlow",sans-serif;font-size:44px;font-weight:500;color:var(--ink);letter-spacing:.5px}
.nav{left:468px;top:57px;display:flex;gap:0}
.nav a{position:absolute;font-family:"Barlow",sans-serif;font-size:16px;font-weight:600;color:var(--ink);text-decoration:none;white-space:nowrap}
.hero-title{left:0;top:340px;width:1200px;text-align:center;font-family:"Barlow",sans-serif;font-weight:700;font-size:54px;color:var(--white);letter-spacing:.5px;text-shadow:0 2px 6px rgba(0,0,0,.25)}

/* services */
.services{left:0;top:660px;width:1200px;height:890px;background:var(--grey-bg)}
.section-intro{font-size:14px;line-height:32px;color:var(--text)}
.card{position:absolute;width:434px;height:202px;background:var(--white);box-shadow:0 3px 10px rgba(0,0,0,.12)}
.card h3{position:absolute;top:31px;font-family:"Barlow",sans-serif;font-weight:500;font-size:19px;color:var(--ink)}
.card p{position:absolute;top:68px;width:260px;font-size:13.5px;line-height:25.5px;color:var(--text)}
.card .icon{position:absolute;top:28px;width:86px;height:86px}
.card.right-icon h3,.card.right-icon p{right:140px;text-align:right}
.card.right-icon .icon{right:26px}
.card.left-icon h3,.card.left-icon p{left:140px}
.card.left-icon .icon{left:26px}

/* partner */
.partner{left:0;top:1550px;width:1200px;height:553px;background:linear-gradient(135deg,#2f8fe6 0%,#2a83d9 50%,#3091e8 100%)}
.partner-title{left:0;top:1640px;width:1200px;text-align:center;font-size:38px;color:var(--white)}
.partner-title b,.partner-title span{color:var(--white)}
.partner-intro{left:240px;top:1740px;width:720px;text-align:center;font-size:14px;line-height:33px;color:#e8f2fc}
.quote-card{left:252px;top:1886px;width:701px;height:271px;background:var(--white);border-radius:6px;box-shadow:0 6px 16px rgba(0,0,0,.14)}
.avatar{left:557px;top:1843px;width:86px;height:86px;border-radius:50%;background:var(--white);box-shadow:0 2px 8px rgba(0,0,0,.15)}
.quote-name{left:0;top:1947px;width:1200px;text-align:center;font-family:"Barlow",sans-serif;font-size:19px;color:var(--blue)}
.quote-text{left:304px;top:1981px;width:620px;text-align:center;font-size:14px;font-style:italic;line-height:27px;color:var(--text)}
.partner-name{font-family:"Barlow",sans-serif;font-size:24px;font-weight:500;color:#8a8f95}

/* career */
.career-art{left:117px;top:2279px;width:433px;height:406px;border-radius:6px;background:linear-gradient(160deg,#f1f5fb 0%,#e3ebf6 55%,#d6e3f3 100%)}
.career-title{left:620px;top:2285px;font-size:34px}
.career-text{left:620px;top:2374px;width:470px;font-size:14px;line-height:28.5px}
.bullets{left:620px;top:2508px;list-style:none}
.bullets li{height:29px;font-size:12.5px;color:var(--ink);display:flex;align-items:center;gap:14px}
.btn-outline{position:absolute;border:2px solid var(--blue);color:var(--blue);font-family:"Barlow",sans-serif;font-weight:600;font-size:14px;display:flex;align-items:center;justify-content:center;background:var(--white)}

/* about */
.about{left:0;top:2797px;width:1200px;height:743px;background:linear-gradient(120deg,#2560ad 0%,#1e58a6 45%,#2866b3 100%)}
.about-photo{left:521px;top:2928px;width:553px;height:479px;border:3px solid var(--white);background:radial-gradient(circle at 52% 35%,#f6c27a 0%,#d07a3a 14%,#4a5f86 38%,#24344f 70%,#1a2438 100%)}
.about-box{left:164px;top:2977px;width:456px;height:378px;background:var(--white)}
.about-box h2{position:absolute;left:32px;top:44px;font-size:38px}
.about-box p{position:absolute;left:32px;top:126px;width:400px;font-size:13.5px;line-height:32px}

/* contact bar */
.contact-bar{left:0;top:3540px;width:1200px;height:175px;background:var(--blue-bright)}
.info{position:absolute;top:3603px;display:flex;gap:16px;align-items:flex-start}
.info h4{font-family:"Barlow",sans-serif;font-weight:700;font-size:18px;color:var(--white);margin-top:-2px}
.info p{font-family:"Barlow",sans-serif;font-size:16px;color:#eaf4fd;margin-top:6px}

/* form */
.kontakt{left:0;top:3715px;width:1200px;height:640px;background:linear-gradient(180deg,#f4f4f4 0%,#eeeeee 100%)}
.kontakt-title{left:0;top:3788px;width:1200px;text-align:center;font-size:38px}
.field{position:absolute;left:164px;width:423px;height:36px;background:var(--white);border:1px solid #c9c9c9;font-size:11.5px;color:#333;padding:12px 0 0 14px}
.message{left:613px;top:3931px;width:423px;height:206px;background:var(--white);border:1px solid #c9c9c9;font-size:11.5px;color:#333;padding:18px 14px}
.submit{left:495px;top:4187px;width:209px;height:51px;background:var(--dark-btn);color:var(--white);font-family:"Barlow",sans-serif;font-weight:700;font-size:22px;display:flex;align-items:center;justify-content:center}

/* footer */
.footer-links{left:0;top:4422px;width:1200px;text-align:center;font-family:"Barlow",sans-serif;font-size:17px;color:var(--ink)}
.copyright{left:0;top:4471px;width:1200px;text-align:center;font-family:"Barlow",sans-serif;font-size:17px;color:var(--ink)}
.social{position:absolute;top:4533px;width:36px;height:36px;border:1.5px solid var(--ink);border-radius:50%}
</style>
</head>
<body>

<!-- hero -->
<section class="abs hero" role="img" aria-label="Photograph of green mountain ridges with a winding path under a bright sky"></section>
<div class="abs logo">VelmaTrix</div>
<nav class="abs nav" aria-label="Hauptmenü">
  <a style="left:0">HOME</a>
  <a style="left:82px">SERVICES</a>
  <a style="left:190px">PARTNER</a>
  <a style="left:294px">KARRIERE</a>
  <a style="left:406px">ÜBER UNS</a>
  <a style="left:516px">KONTAKT</a>
</nav>
<svg class="abs" style="left:579px;top:262px" width="60" height="60" viewBox="0 0 60 60" aria-hidden="true">
  <circle cx="30" cy="30" r="28" fill="none" stroke="#fff" stroke-width="2.5"/>
  <path d="M24 19 L41 30 L24 41 Z" fill="none" stroke="#fff" stroke-width="2.5" stroke-linejoin="round"/>
</svg>
<h1 class="abs hero-title">VELMATRIX IT CONSULTING</h1>
<svg class="abs" style="left:100px;top:324px" width="30" height="30" viewBox="0 0 30 30" aria-hidden="true"><circle cx="15" cy="15" r="14" fill="rgba(0,0,0,.55)"/><path d="M17 9 L11 15 L17 21" fill="none" stroke="#fff" stroke-width="2"/></svg>
<svg class="abs" style="left:1070px;top:324px" width="30" height="30" viewBox="0 0 30 30" aria-hidden="true"><circle cx="15" cy="15" r="14" fill="rgba(0,0,0,.55)"/><path d="M13 9 L19 15 L13 21" fill="none" stroke="#fff" stroke-width="2"/></svg>

<!-- services -->
<section class="abs services"></section>
<svg class="abs" style="left:540px;top:620px" width="120" height="42" viewBox="0 0 120 42" aria-hidden="true">
  <path d="M0 42 C30 42 40 10 60 10 C80 10 90 42 120 42 Z" fill="#efefef"/>
  <path d="M60 26 V48 M53 41 L60 48 L67 41" fill="none" stroke="#2d8ae2" stroke-width="2" transform="translate(0,-8)"/>
</svg>

<h2 class="abs heading" style="left:144px;top:767px;font-size:38px"><b>OUR</b> <span>SERVICES</span></h2>
<div class="rule" style="left:144px;top:835px;width:86px"></div>
<p class="abs section-intro" style="left:144px;top:858px;width:440px">Sed ut perspiciatis unde omnis iste natus error sit voluptatem accusantium doloremque laudantium, totam rem aperiam, eaque ipsa quae ab illo inventore veritatis et quasi</p>

<article class="card left-icon" style="left:620px;top:760px">
  <svg class="icon" viewBox="0 0 86 86" aria-hidden="true"><circle cx="43" cy="43" r="41" fill="none" stroke="#2d8ae2" stroke-width="2.5"/><rect x="25" y="30" width="32" height="22" fill="none" stroke="#2d8ae2" stroke-width="2"/><circle cx="52" cy="48" r="7" fill="none" stroke="#2d8ae2" stroke-width="2"/><path d="M57 53 L63 59" stroke="#2d8ae2" stroke-width="2.5"/><path d="M30 46 L36 40 L41 44 L47 36" fill="none" stroke="#2d8ae2" stroke-width="2"/></svg>
  <h3>OUTPUT MANAGEMENT</h3>
  <p>Sed ut perspiciatis unde omnis iste natus error sit voluptatem accusantium doloremque laudantium, totam rem aperiam, eaque ipsa quae ab illo</p>
</article>

<article class="card right-icon" style="left:144px;top:991px">
  <svg class="icon" viewBox="0 0 86 86" aria-hidden="true"><circle cx="43" cy="43" r="41" fill="none" stroke="#2d8ae2" stroke-width="2.5"/><circle cx="43" cy="32" r="6" fill="none" stroke="#2d8ae2" stroke-width="2"/><circle cx="30" cy="40" r="5" fill="none" stroke="#2d8ae2" stroke-width="2"/><circle cx="56" cy="40" r="5" fill="none" stroke="#2d8ae2" stroke-width="2"/><path d="M33 58 C33 46 53 46 53 58 M21 58 C21 49 34 48 36 52 M65 58 C65 49 52 48 50 52" fill="none" stroke="#2d8ae2" stroke-width="2"/></svg>
  <h3>OUTSOURCING</h3>
  <p>Sed ut perspiciatis unde omnis iste natus error sit voluptatem accusantium doloremque laudantium, totam rem aperiam, eaque ipsa quae ab illo</p>
</article>

<article class="card left-icon" style="left:620px;top:991px">
  <svg class="icon" viewBox="0 0 86 86" aria-hidden="true"><circle cx="43" cy="43" r="41" fill="none" stroke="#2d8ae2" stroke-width="2.5"/><rect x="24" y="26" width="38" height="28" fill="none" stroke="#2d8ae2" stroke-width="2"/><path d="M20 60 H66" stroke="#2d8ae2" stroke-width="2.5"/><path d="M37 35 L32 40 L37 45 M49 35 L54 40 L49 45" fill="none" stroke="#2d8ae2" stroke-width="2"/></svg>
  <h3>ENTWICKLUNG</h3>
  <p>Sed ut perspiciatis unde omnis iste natus error sit voluptatem accusantium doloremque laudantium, totam rem aperiam, eaque ipsa quae ab illo</p>
</article>

<article class="card right-icon" style="left:144px;top:1223px">
  <svg class="icon" viewBox="0 0 86 86" aria-hidden="true"><circle cx="43" cy="43" r="41" fill="none" stroke="#2d8ae2" stroke-width="2.5"/><rect x="36" y="24" width="28" height="20" fill="none" stroke="#2d8ae2" stroke-width="2"/><path d="M41 39 V34 M47 39 V30 M53 39 V32 M59 39 V28" stroke="#2d8ae2" stroke-width="2"/><circle cx="30" cy="40" r="5" fill="none" stroke="#2d8ae2" stroke-width="2"/><path d="M22 62 V52 C22 47 38 47 38 52 V62" fill="none" stroke="#2d8ae2" stroke-width="2"/></svg>
  <h3>BUSINESS ANALYST</h3>
  <p>Sed ut perspiciatis unde omnis iste natus error sit voluptatem accusantium doloremque laudantium, totam rem aperiam, eaque ipsa quae ab illo</p>
</article>

<article class="card left-icon" style="left:620px;top:1223px">
  <svg class="icon" viewBox="0 0 86 86" aria-hidden="true"><circle cx="43" cy="43" r="41" fill="none" stroke="#2d8ae2" stroke-width="2.5"/><rect x="22" y="24" width="42" height="26" fill="none" stroke="#2d8ae2" stroke-width="2"/><path d="M28 44 L36 36 L42 41 L52 31" fill="none" stroke="#2d8ae2" stroke-width="2"/><path d="M43 50 V56 M33 64 L43 56 L53 64" fill="none" stroke="#2d8ae2" stroke-width="2"/></svg>
  <h3>SCHULUNGEN</h3>
  <p>Sed ut perspiciatis unde omnis iste natus error sit voluptatem accusantium doloremque laudantium, totam rem aperiam, eaque ipsa quae ab illo</p>
</article>

<!-- partner -->
<section class="abs partner"></section>
<h2 class="abs heading partner-title"><b>OUR</b> <span>PARTNER</span></h2>
<div class="rule" style="left:557px;top:1711px;width:86px;background:#fff"></div>
<p class="abs partner-intro">Sed ut perspiciatis unde omnis iste natus error sit voluptatem accusantium doloremque laudantium, totam rem aperiam, eaque ipsa quae ab illo inventore veritatis et quasi</p>
<svg class="abs" style="left:184px;top:1992px" width="26" height="44" viewBox="0 0 26 44" aria-hidden="true"><path d="M23 2 L3 22 L23 42" fill="none" stroke="#fff" stroke-width="2"/></svg>
<svg class="abs" style="left:995px;top:1992px" width="26" height="44" viewBox="0 0 26 44" aria-hidden="true"><path d="M3 2 L23 22 L3 42" fill="none" stroke="#fff" stroke-width="2"/></svg>
<div class="abs quote-card"></div>
<div class="abs avatar"></div>
<svg class="abs" style="left:563px;top:1849px" width="74" height="74" viewBox="0 0 74 74" aria-hidden="true"><circle cx="37" cy="37" r="35" fill="#fff"/><circle cx="37" cy="28" r="12" fill="#1d2330"/><path d="M15 58 C17 42 57 42 59 58 Z" fill="#1d2330"/></svg>
<div class="abs quote-name">Jorin Havel</div>
<svg class="abs" style="left:286px;top:1984px" width="16" height="12" viewBox="0 0 16 12" aria-hidden="true"><path d="M1 12 V6 L4 0 H6 L4 6 H7 V12 Z M9 12 V6 L12 0 H14 L12 6 H15 V12 Z" fill="#222"/></svg>
<p class="abs quote-text">Nemo enim ipsam voluptatem quia voluptas sit aspernatur aut odit aut fugit, sed quia constur magni dolores eos qui ratione voluptatem sequi nesciunt. Neque porro quisquam est, qui drem ipsum quia dolor sit amet, consectetur, adipisci velit, sed quia non numquam</p>
<svg class="abs" style="left:880px;top:2040px" width="16" height="12" viewBox="0 0 16 12" aria-hidden="true"><path d="M1 0 V6 L4 12 H6 L4 6 H7 V0 Z M9 0 V6 L12 12 H14 L12 6 H15 V0 Z" fill="#222"/></svg>
<div class="abs partner-name" style="left:482px;top:2088px">Norvanta</div>
<div class="abs partner-name" style="left:618px;top:2088px">Kelpiro</div>

<!-- career -->
<div class="abs career-art" role="img" aria-label="Illustration of a team working at desks in front of a large analytics dashboard"></div>
<h2 class="abs heading career-title"><b>KARRIERE</b></h2>
<div class="rule" style="left:620px;top:2347px;width:80px"></div>
<p class="abs career-text">Sed ut perspiciatis unde omnis iste natus error sit voluptatem atium doloremque laudantium, totam rem aperiam, eaque ipsa quae ab illo inventore veritatis et quasi architecto beatae vitae dicta sunt explicabo. Nemo enim ipsam voluptatem</p>
<ul class="abs bullets">
  <li><svg width="14" height="14" viewBox="0 0 14 14" aria-hidden="true"><circle cx="7" cy="7" r="6" fill="none" stroke="#2d8ae2" stroke-width="1.5"/><path d="M7 4 V10 M4 7 H10" stroke="#2d8ae2" stroke-width="1.5"/></svg>Lorem ipsum dolor sit amet. consectetur</li>
  <li><svg width="14" height="14" viewBox="0 0 14 14" aria-hidden="true"><circle cx="7" cy="7" r="6" fill="none" stroke="#2d8ae2" stroke-width="1.5"/><path d="M7 4 V10 M4 7 H10" stroke="#2d8ae2" stroke-width="1.5"/></svg>Donec ultricies diam quis quam lobortis, vitae</li>
  <li><svg width="14" height="14" viewBox="0 0 14 14" aria-hidden="true"><circle cx="7" cy="7" r="6" fill="none" stroke="#2d8ae2" stroke-width="1.5"/><path d="M7 4 V10 M4 7 H10" stroke="#2d8ae2" stroke-width="1.5"/></svg>Cras porttitor ligula quis sapien eleifend ullamcorper.</li>
</ul>
<a class="btn-outline" style="left:620px;top:2616px;width:152px;height:42px">APPLY NOW</a>

<!-- about -->
<section class="abs about" role="img" aria-label="Faint photograph of a team meeting in an office, tinted blue"></section>
<div class="abs about-photo" role="img" aria-label="Photograph of a hand holding a glowing light bulb surrounded by network lines"></div>
<div class="abs about-box">
  <h2 class="heading"><b>ÜBER UNS</b></h2>
  <p>Sed ut perspiciatis unde omnis iste natus error sit voluptatem accntium doloremque laudantium, totam rem aperiam, eaque ipsa quae ab illo itore veritatis et quasi architecto beatae vitae dicta sunt explicabo. Nemo enim ipsam voluptatem quia voluptas sit aspernatur</p>
  <a class="btn-outline" style="left:32px;top:302px;width:143px;height:37px;font-size:13.5px">LEARN MORE</a>
</div>

<!-- contact bar -->
<section class="abs contact-bar"></section>
<div class="info" style="left:149px">
  <svg width="44" height="44" viewBox="0 0 44 44" aria-hidden="true"><circle cx="22" cy="22" r="20" fill="none" stroke="#fff" stroke-width="2"/><path d="M22 33 C16 26 15 23 15 20 A7 7 0 0 1 29 20 C29 23 28 26 22 33 Z" fill="none" stroke="#fff" stroke-width="2"/><circle cx="22" cy="20" r="2.5" fill="#fff"/></svg>
  <div><h4>Address:</h4><p>14 Ferngate Lane, Ostbrück</p></div>
</div>
<div class="info" style="left:526px">
  <svg width="44" height="44" viewBox="0 0 44 44" aria-hidden="true"><circle cx="22" cy="22" r="20" fill="none" stroke="#fff" stroke-width="2"/><path d="M15 14 L19 13 L21 18 L18.5 20 C20 23 21 24 24 25.5 L26 23 L31 25 L30 29 C22 30 14 22 15 14 Z" fill="none" stroke="#fff" stroke-width="2" stroke-linejoin="round"/></svg>
  <div><h4>Phone:</h4><p>(040) 5127 3380</p></div>
</div>
<div class="info" style="left:801px">
  <svg width="44" height="44" viewBox="0 0 44 44" aria-hidden="true"><circle cx="22" cy="22" r="20" fill="none" stroke="#fff" stroke-width="2"/><rect x="13" y="15" width="18" height="14" rx="1" fill="none" stroke="#fff" stroke-width="2"/><path d="M13 16 L22 23 L31 16" fill="none" stroke="#fff" stroke-width="2"/></svg>
  <div><h4>Email:</h4><p>info@velmatrix.com</p></div>
</div>

<!-- kontakt -->
<section class="abs kontakt" role="img" aria-label="Faint photograph of a desk with a tablet, phone and coffee cup"></section>
<h2 class="abs heading kontakt-title"><b>KONTAKT</b></h2>
<div class="rule" style="left:568px;top:3859px;width:64px"></div>
<div class="field" style="top:3933px">Name *</div>
<div class="field" style="top:3987px">Phone *</div>
<div class="field" style="top:4043px">Email *</div>
<div class="field" style="top:4097px">Subject *</div>
<div class="abs message">Message</div>
<div class="abs submit">SUBMIT</div>

<!-- footer -->
<nav class="abs footer-links">Home | Services | Partner | Karriere | Über uns | Kontakt</nav>
<p class="abs copyright">VelmaTrix © 2019 All Rights Reserved | Privacy Policy</p>
<span class="social" style="left:533px" aria-label="Social profile"></span>
<span class="social" style="left:582px" aria-label="Social profile"></span>
<span class="social" style="left:631px" aria-label="Social profile"></span>

</body>
</html>
```